Dynamic Business Card for Sports Supplements Company

Hi! I'm looking for an awesome business card to match my existing sports supplement company. I have uploaded my current company logo and screenshot of the front page of my website.

I would like to have something dynamic and interesting and utilize the colors in the website - the reds and purples

The business card should be double sided and focus on a unique eye-catching design on the back and include all the relevant company info.

Most importantly, it should say somewhere: "Sign up on our website for a coupon code."

Target Market(s)

Mostly for women gym goers but it shouldn't be too feminine. It should be in keeping with the website design. It should flow and clearly be connected to it

Industry/Entity Type

Business

Contact Information for Business Card

Lorraine K. Vestal
CEO
LVestal@Quorvanexco.com
www.quorvanexco.com
555.417.3820
P.O. Box 47315
Alder, Calvora 00000

Sign up on our website for a coupon code

Font styles to use
Serif
Sans Serif
Other font styles liked:
• Novecento font family and "Quorvanex" is in AR Destine font

Requirements
Must have
• One side should be a bold Quorvanex logo design. Even just the symbol itself may be o.k. (see attached file)

```html
<!DOCTYPE html>
<html lang="en">
<head>
<meta charset="utf-8">
<title>Quorvanex Business Card</title>
<link rel="stylesheet" href="https://fonts.googleapis.com/css2?family=Source+Sans+3:ital,wght@0,400;0,600;0,700;1,400&display=swap">
<style>
  :root {
    --bg: #e7e5e2;
    --card-black: #000000;
    --brand-red: #ed1c24;
    --white: #ffffff;
    --muted: #8a8a8a;
    --faint: #1c1c1c;
    --faint-red: #1e0306;
  }
  * { margin: 0; padding: 0; box-sizing: border-box; }
  html, body {
    width: 1200px; height: 987px; overflow: hidden;
    background: var(--bg);
    font-family: "Source Sans 3", "Myriad Pro", sans-serif;
  }
  .canvas { position: relative; width: 1200px; height: 987px; }
  .card {
    position: absolute; left: 293px; width: 615px; height: 352px;
    background: var(--card-black); overflow: hidden;
    box-shadow: 0 3px 10px rgba(0,0,0,.35);
  }
  .card--front { top: 129px; }
  .card--back { top: 505px; }
  .card svg.card-shapes { position: absolute; inset: 0; }

  .brand { position: absolute; color: var(--white); }
  .brand__mark {
    display: block; width: 40px; height: 40px; background: var(--brand-red);
    margin: 0 auto 14px;
  }
  .brand__name {
    font-weight: 700; font-size: 33px; letter-spacing: 1px;
    text-transform: uppercase; line-height: 1; text-align: center;
  }
  .brand__tagline {
    font-size: 9.5px; letter-spacing: 2.4px; color: var(--muted);
    text-transform: uppercase; margin-top: 3px; white-space: nowrap;
    text-align: center;
  }
  .card--front .brand { left: 44px; top: 52px; width: 214px; }

  .contact {
    position: absolute; right: 25px; top: 182px; text-align: right;
    color: var(--white);
  }
  .contact__name { font-size: 22px; font-weight: 600; line-height: 1.1; }
  .contact__role { font-size: 16px; margin-top: 3px; margin-bottom: 17px; }
  .contact__line {
    font-size: 15px; line-height: 23.5px;
    display: flex; justify-content: flex-end; align-items: center; gap: 6px;
  }
  .contact__line svg { width: 14px; height: 14px; flex: none; }

  .back-decor { position: absolute; left: 12px; top: 12px; width: 320px; height: 328px; }
  .card--back .brand { left: 355px; top: 258px; width: 230px; }
  .card--back .brand__name { font-size: 31px; text-align: left; }
  .card--back .brand__tagline { text-align: left; letter-spacing: 2.6px; }
  .brand__offer { font-style: italic; font-size: 12.5px; margin-top: 5px; white-space: nowrap; }
</style>
</head>
<body>
<main class="canvas">

  <section class="card card--front" aria-label="Business card front">
    <svg class="card-shapes" viewBox="0 0 615 352" width="615" height="352" aria-hidden="true">
      <polygon points="0,240 152,314 615,0 615,352 0,352" fill="var(--brand-red)"/>
      <polyline points="0,229 152,304 615,-9" fill="none" stroke="var(--white)" stroke-width="5"/>
    </svg>

    <div class="brand">
      <span class="brand__mark"></span>
      <div class="brand__name">Quorvanex</div>
      <div class="brand__tagline">Your strength companion</div>
    </div>

    <div class="contact">
      <div class="contact__name">Lorraine K. Vestal</div>
      <div class="contact__role">CEO</div>
      <div class="contact__line">555.417.3820
        <svg viewBox="0 0 16 16" aria-hidden="true"><path fill="#fff" d="M3.5 1.5l2.6 0 1 3.4-1.7 1.2a9 9 0 0 0 4.5 4.5l1.2-1.7 3.4 1v2.6c0 .8-.7 1.5-1.5 1.5A12.5 12.5 0 0 1 2 3c0-.8.7-1.5 1.5-1.5z"/></svg>
      </div>
      <div class="contact__line">LVestal@Quorvanexco.com
        <svg viewBox="0 0 16 16" aria-hidden="true"><rect x="1" y="3" width="14" height="10" fill="#fff"/><polyline points="1,3 8,9 15,3" fill="none" stroke="var(--brand-red)" stroke-width="1.4"/></svg>
      </div>
      <div class="contact__line">www.quorvanexco.com
        <svg viewBox="0 0 16 16" aria-hidden="true"><circle cx="8" cy="8" r="7" fill="#fff"/><path d="M8 1v14M1 8h14M3 4.5h10M3 11.5h10" stroke="var(--brand-red)" stroke-width="1" fill="none"/></svg>
      </div>
      <div class="contact__line">P.O. Box 47315, Alder, Calvora 00000</div>
    </div>
  </section>

  <section class="card card--back" aria-label="Business card back">
    <svg class="back-decor" viewBox="0 0 320 328" aria-hidden="true">
      <rect x="0" y="0" width="320" height="328" fill="var(--faint)"/>
      <rect x="0" y="0" width="320" height="110" fill="var(--faint-red)"/>
    </svg>
    <div class="brand">
      <div class="brand__name">Quorvanex</div>
      <div class="brand__tagline">Your strength companion</div>
      <div class="brand__offer">Sign up on our website for a coupon code</div>
    </div>
  </section>

</main>
</body>
</html>
```